equestrian poster

Could you make the poster an elete looking poster for a sports event using the building on the back ground and photo shop the horse there also please make an sporty luxery poster
the dates for next year are 27th till 31 st may and 16 till 19 plus 23rd till 26 juli

our colors are green and gray

Target Market(s)

tourist and public

Industry/Entity Type

equestrian event interna

Other font styles liked:
• caslon classico font

Colors
00AB8E
00BBA5
67D7C9
C6EFE9
E9F9F6

```html
<!DOCTYPE html>
<html lang="en">
<head>
<meta charset="utf-8">
<title>CH van Linden – Equestrian Event Poster</title>
<link rel="stylesheet" href="https://fonts.googleapis.com/css2?family=Libre+Caslon+Text:wght@400;700&family=Montserrat:wght@400;500;800&family=Permanent+Marker&display=swap">
<style>
  :root {
    --stage: #d6d2d0;
    --mist-top: #c4dfdc;
    --mist-mid: #d9ecea;
    --paper: #f7fbfb;
    --brand-green: #0b4a22;
    --gold: #a48b68;
    --ink: #1e2a26;
    --rule: #86ad9d;
    --photo-sky: #c9dbe0;
    --photo-city: #a9b2c4;
    --photo-horse: #7a3b1f;
    --photo-horse-dark: #5a2a15;
    --photo-dust: #e2e9e7;
    --white: #ffffff;
  }
  * { margin: 0; padding: 0; box-sizing: border-box; }
  html, body {
    width: 1200px; height: 2518px; overflow: hidden;
    background: var(--stage);
  }
  .poster {
    position: absolute; left: 40px; top: 468px;
    width: 1120px; height: 1581px; overflow: hidden;
    background: linear-gradient(180deg, var(--mist-top) 0%, var(--mist-mid) 45%, #e8f3f3 72%, var(--paper) 85%, var(--paper) 100%);
  }
  .hero-photo {
    position: absolute; left: 100px; top: 470px; width: 920px; height: 700px;
    background: linear-gradient(180deg,
      var(--photo-sky) 0%,
      var(--photo-city) 24%,
      var(--photo-horse) 46%,
      var(--photo-horse-dark) 66%,
      var(--photo-horse) 80%,
      var(--photo-dust) 100%);
    -webkit-mask-image: linear-gradient(90deg, transparent 0%, #000 10%, #000 90%, transparent 100%);
    mask-image: linear-gradient(90deg, transparent 0%, #000 10%, #000 90%, transparent 100%);
    opacity: 0.85;
  }
  .since {
    position: absolute; left: 0; right: 0; top: 135px; text-align: center;
    font-family: "Libre Caslon Text", serif; font-weight: 700;
    font-size: 48px; letter-spacing: 3px; color: var(--gold);
  }
  .title {
    position: absolute; left: 0; right: 0; top: 215px; text-align: center;
    font-family: "Permanent Marker", cursive; font-weight: 400; color: var(--brand-green);
    font-size: 168px; line-height: 172px; letter-spacing: 2px;
  }
  .title span { display: block; }
  .title .line2 { margin-left: 30px; }
  .brand {
    position: absolute; left: 0; right: 0; top: 1028px; text-align: center;
  }
  .brand-dot {
    display: block; width: 100px; height: 100px; margin: 0 auto 10px;
    border-radius: 50%; background: var(--brand-green);
  }
  .brand-name {
    font-family: "Libre Caslon Text", serif; font-size: 38px; color: var(--brand-green);
  }
  .dates {
    position: absolute; left: 51px; width: 1015px; top: 1215px;
    display: flex; justify-content: space-between;
  }
  .date {
    width: 320px; text-align: center; font-family: "Montserrat", sans-serif; color: var(--ink);
  }
  .date-days { font-weight: 800; font-size: 55px; line-height: 70px; color: var(--brand-green); }
  .date-month { font-weight: 500; font-size: 52px; line-height: 72px; }
  .rule {
    position: absolute; left: 51px; width: 1015px; top: 1375px; height: 3px; background: var(--rule);
  }
  .classes {
    position: absolute; left: 0; right: 0; top: 1403px; text-align: center;
    font-family: "Montserrat", sans-serif; font-size: 24px; color: var(--ink);
  }
  .footer-band {
    position: absolute; left: 0; right: 0; bottom: 0; height: 111px;
    background: var(--brand-green); color: var(--white);
    display: flex; align-items: center; justify-content: space-between;
    padding: 0 50px;
    font-family: "Montserrat", sans-serif;
  }
  .website { font-size: 36px; font-weight: 500; letter-spacing: 1px; }
  .socials { display: flex; gap: 22px; font-size: 24px; font-weight: 500; }
</style>
</head>
<body>
  <main class="poster">
    <div class="hero-photo" role="img" aria-label="Photograph of a rider on a galloping chestnut horse kicking up dust, with a misty city skyline behind"></div>
    <p class="since">SINCE 2005</p>
    <h1 class="title"><span class="line1">CH VAN</span><span class="line2">LINDEN</span></h1>
    <div class="brand">
      <span class="brand-dot"></span>
      <span class="brand-name">C.H. van Linden</span>
    </div>
    <section class="dates">
      <div class="date"><div class="date-days">27 - 31</div><div class="date-month">May 2026</div></div>
      <div class="date"><div class="date-days">16 - 19</div><div class="date-month">July 2026</div></div>
      <div class="date"><div class="date-days">23 - 26</div><div class="date-month">July 2026</div></div>
    </section>
    <div class="rule"></div>
    <p class="classes">CSI 2* / CSI 1 */ CSI 1* YH</p>
    <footer class="footer-band">
      <span class="website">www.chvanlinden.nl</span>
      <span class="socials"><span>Snapwall</span><span>Facepage</span></span>
    </footer>
  </main>
</body>
</html>
```